Black Car Limousine transportation business in Naples Florida

Always stand for my reliability and RVD stands for Love, K and M are the first initials of my children's names. It should show professionalism and a dedication to customer service. We keep our clients identities private. Show our professionalism. We are Black car Black tie company. We service transportation on a reserve basis to and from residents, airports, casinos, hotels,

Target Market(s)

It is a Private car service. High end clients. Businesses, Celebrity and athletes. Service to airports, hotels, special events.

Industry/Entity Type

Business

Contact Information for Business Card

A pearl metallic or Luster card. Standard business card size. Would like the name, Company email, show we take credit cards and phone number. Currently I don't have a website but will like to add later.

Logo Text

STEADFAST RVD TRANSPORTATION

Font styles to use
Serif

Colors
eaeaea
000000

Requirements
Must have
• Must have Company email, show we take credit cards and phone number. Currently I don't have a website but will like to add later.
Nice to have
• Would like to stay with a black and white theme. Open to some color trim.
Should not have
• Open to suggestions

```html
<!DOCTYPE html>
<html lang="en">
<head>
<meta charset="utf-8">
<title>Steadfast RVD Transportation – Business Card</title>
<link rel="stylesheet" href="https://fonts.googleapis.com/css2?family=PT+Serif:wght@400;700&display=swap">
<style>
  :root {
    --stage: #000000;
    --card-light: #f2f2f2;
    --card-dark: #353535;
    --ink-dark: #333333;
    --ink-light: #cfcfcf;
    --photo-top: #3a3a3a;
    --photo-mid: #1c1c1c;
    --photo-low: #0b0b0b;
  }
  * { margin: 0; padding: 0; box-sizing: border-box; }
  html, body {
    width: 1200px; height: 900px; overflow: hidden;
    background: var(--stage);
    font-family: "PT Serif", Georgia, serif;
  }
  .canvas { position: relative; width: 1200px; height: 900px; }

  .card {
    position: absolute; top: 200px;
    width: 310px; height: 502px; overflow: hidden;
  }
  .card--front {
    left: 265px; background: var(--card-light); color: var(--ink-dark);
    border-radius: 42px 0 42px 0;
  }
  .card--back {
    left: 641px; background: var(--card-dark); color: var(--ink-light);
    border-radius: 0 42px 0 42px;
  }

  .wordmark {
    position: absolute; left: 26px; top: 46px;
    line-height: 1; white-space: nowrap;
  }
  .card--back .wordmark { left: 22px; top: 60px; }
  .wordmark__top { display: block; font-size: 16px; letter-spacing: 3px; }
  .wordmark__main { display: block; font-size: 66px; font-weight: 700; letter-spacing: 1px; margin-top: 2px; }
  .wordmark__base { display: block; font-size: 24px; letter-spacing: 0.3px; margin-top: 4px; }

  .contact { position: absolute; left: 27px; top: 318px; font-size: 13px; line-height: 16px; }
  .contact__name { font-size: 16px; font-weight: 700; letter-spacing: 0.3px; line-height: 20px; }
  .contact__role { margin-top: 3px; }
  .contact__address { margin-top: 18px; }
  .contact__lines { margin-top: 11px; list-style: none; }
  .contact__lines li { display: flex; align-items: center; gap: 7px; height: 19px; }
  .contact__lines svg { width: 11px; height: 10px; fill: var(--ink-dark); flex: none; }

  .vehicle-photo {
    position: absolute; left: 0; bottom: 0; width: 310px; height: 252px;
    background:
      radial-gradient(ellipse at 60% 45%, var(--photo-top) 0%, var(--photo-mid) 55%, transparent 80%),
      linear-gradient(180deg, var(--card-dark) 0%, var(--photo-mid) 40%, var(--photo-low) 100%);
  }
</style>
</head>
<body>
<main class="canvas">

  <section class="card card--front">
    <div class="wordmark">
      <span class="wordmark__top">STEADFAST</span>
      <span class="wordmark__main">RVD</span>
      <span class="wordmark__base">TRANSPORTATION</span>
    </div>

    <div class="contact">
      <p class="contact__name">JOHN SMITH</p>
      <p class="contact__role">Managing Director</p>
      <p class="contact__address">1234, Address Goes Here<br>Country Name, 123456</p>
      <ul class="contact__lines">
        <li>
          <svg viewBox="0 0 10 10" aria-hidden="true"><path d="M1 3.2C1 2 2 1.5 5 1.5S9 2 9 3.2v1H7V3.4H3v.8H1z"/><path d="M2.2 5h5.6l.7 3.5H1.5z"/></svg>
          <span>823-456-7890</span>
        </li>
        <li>
          <svg viewBox="0 0 10 10" aria-hidden="true"><path d="M1 2.5h8v5H1z M1.4 2.9 5 5.6l3.6-2.7" stroke="#f2f2f2" stroke-width="0.8"/></svg>
          <span>info@youremail.com</span>
        </li>
        <li>
          <svg viewBox="0 0 11 10" aria-hidden="true"><rect x="0.5" y="1.5" width="10" height="7" rx="1"/><rect x="0.5" y="3" width="10" height="1.4" fill="#f2f2f2"/></svg>
          <span>All major credit cards accepted</span>
        </li>
      </ul>
    </div>
  </section>

  <section class="card card--back">
    <div class="wordmark">
      <span class="wordmark__top">STEADFAST</span>
      <span class="wordmark__main">RVD</span>
      <span class="wordmark__base">TRANSPORTATION</span>
    </div>
    <div class="vehicle-photo" role="img" aria-label="Photograph of a black luxury SUV, front three-quarter view"></div>
  </section>

</main>
</body>
</html>
```